"Vine Hollow Excursions" is a top notch Santa Barbara County Wine Tour company.

We provide scenic, boutique and custom wine tours. I need the card to be clean and classy. I will provide our logo. I would like the logo to cover the back side of the card as an option and would like to see a couple color options other then our signature green and gold. I would like to see some creative options and let the designers come up with options.
I need cards for myself and my team. The final design should communicate "An authentic and boutique wine tour experience"
Please use my website for reference www.vinehollowexcursions.example

Target Market(s)

We have a wide range of clients from millennials to baby boomers

Industry/Entity Type

Tour

Contact Information for Business Card

Contact info:
Dale Morton
805-219-6384
info@vinehollowexcursions.example
vinehollowexcursions.example

Colors

Designer to choose colors to be used in the design.

Requirements
Must have
• my logo
Nice to have
• *I would like to have the backside side with the logo and the company statement
• "An authentic and boutique wine tour experience" as an option.
• *I would also like to see what the designers can create!
• *I would like to see an option that incorporates or social: instagram, yelp, trip advisor
Should not have
• I do not want it too busy.

```html
<!DOCTYPE html>
<html lang="en">
<head>
<meta charset="utf-8">
<title>Vine Hollow Excursions – Business Card</title>
<link rel="stylesheet" href="https://fonts.googleapis.com/css2?family=Roboto:wght@400;500&family=Roboto+Condensed:wght@400;500&display=swap">
<style>
  :root {
    --backdrop: #ece9e4;
    --card-white: #f7f7f7;
    --card-grey: #dedede;
    --vine-green: #246840;
    --gold: #b99a6c;
    --gold-light: #d8c4a0;
    --text-grey: #4d4d4d;
    --tan-centre: #baa17c;
    --tan-edge: #84725f;
    --social-top: #9a9a9a;
    --social-bottom: #6a6a6a;
  }
  * { box-sizing: border-box; margin: 0; padding: 0; }
  html, body { width: 1200px; height: 960px; overflow: hidden; }
  body { background: var(--backdrop); position: relative; font-family: "Roboto", Arial, sans-serif; }

  .card { position: absolute; width: 600px; height: 342px; box-shadow: 0 3px 8px rgba(0,0,0,.25); overflow: hidden; }

  .card-front { left: 302px; top: 129px; background: linear-gradient(100deg, var(--card-white) 0%, var(--card-grey) 100%); }
  .brand-name {
    position: absolute; right: 44px; top: 100px; width: 240px; text-align: center;
    font-family: "Roboto Condensed", Arial, sans-serif; font-weight: 500; font-size: 24px;
    color: var(--vine-green); letter-spacing: .5px;
  }
  .holder-name {
    position: absolute; left: 33px; top: 193px;
    font-family: "Roboto Condensed", Arial, sans-serif; font-weight: 500; font-size: 27px;
    color: var(--vine-green); text-transform: uppercase;
  }
  .divider { position: absolute; left: 33px; top: 232px; width: 523px; height: 1px; background: var(--gold); }
  .contact-list { position: absolute; left: 33px; top: 248px; list-style: none; }
  .contact-list li { display: flex; align-items: center; height: 19px; font-size: 14.5px; color: var(--text-grey); }
  .contact-list svg { width: 13px; height: 13px; margin-right: 10px; fill: var(--vine-green); flex: none; }
  .social-row { position: absolute; right: 42px; top: 274px; display: flex; gap: 7px; }
  .social-tile { width: 27px; height: 27px; border-radius: 4px; background: linear-gradient(var(--social-top), var(--social-bottom)); }
  .accent-band { position: absolute; left: 0; bottom: 0; width: 100%; height: 9px; display: flex; }
  .accent-band .green { width: 390px; background: var(--vine-green); }
  .accent-band .gap { width: 4px; background: #fff; transform: skewX(-20deg); }
  .accent-band .gold { flex: 1; background: linear-gradient(90deg, #9e9c98, var(--gold-light)); }

  .card-back { left: 300px; top: 488px; width: 598px; background: radial-gradient(ellipse at 55% 35%, var(--tan-centre) 0%, var(--tan-edge) 85%); }
  .back-brand {
    position: absolute; left: 0; top: 110px; width: 100%; text-align: center;
    font-family: "Roboto Condensed", Arial, sans-serif; font-weight: 500; font-size: 40px;
    color: var(--vine-green);
  }
  .tagline {
    position: absolute; left: 0; top: 235px; width: 100%; text-align: center;
    font-family: "Roboto Condensed", Arial, sans-serif; font-size: 16.5px; color: var(--vine-green);
  }
</style>
</head>
<body>
  <section class="card card-front">
    <div class="brand-name">Vine Hollow Excursions</div>
    <h1 class="holder-name">Dale Morton</h1>
    <div class="divider"></div>
    <ul class="contact-list">
      <li><svg viewBox="0 0 24 24"><path d="M6.6 10.8a15.1 15.1 0 0 0 6.6 6.6l2.2-2.2c.3-.3.7-.4 1-.2 1.1.4 2.3.6 3.6.6.6 0 1 .4 1 1V20c0 .6-.4 1-1 1A17 17 0 0 1 3 4c0-.6.4-1 1-1h3.5c.6 0 1 .4 1 1 0 1.3.2 2.5.6 3.6.1.3 0 .7-.2 1z"/></svg>805-219-6384</li>
      <li><svg viewBox="0 0 24 24"><path d="M2 5h20v14H2z"/><path d="M3 6l9 6.3L21 6" stroke="#eee" stroke-width="1.6" fill="none"/></svg>info@vinehollowexcursions.example</li>
      <li><svg viewBox="0 0 24 24"><circle cx="12" cy="12" r="10"/><path d="M8 6c2 1 1 3 3 4s1 3-1 3-2 3 0 5M15 4c-1 2 1 3 3 3m-3 8c2 0 3 1 2 3" stroke="#eee" stroke-width="1.6" fill="none"/></svg>vinehollowexcursions.example</li>
    </ul>
    <div class="social-row" aria-label="Social profiles">
      <span class="social-tile"></span><span class="social-tile"></span><span class="social-tile"></span><span class="social-tile"></span><span class="social-tile"></span>
    </div>
    <div class="accent-band"><span class="green"></span><span class="gap"></span><span class="gold"></span></div>
  </section>

  <section class="card card-back">
    <div class="back-brand">Vine Hollow Excursions</div>
    <p class="tagline">A genuine &amp; intimate valley tasting journey</p>
  </section>
</body>
</html>
```